New Business Card Design Project

Need a design that will create an impact / strong impression towards our clients for our business. We are in the lighting business and we do lighting retrofits for large commercial to industrial clientele.

Target Market(s)

Lighting Industry

Industry/Entity Type

Business

Font styles to use
Other font styles liked:
• we would like to use the font on our logo, not sure what it is though..

Requirements
Must have
• Our logo.
Nice to have
• We are open to suggestions that have to do with lighting.

```html
<!DOCTYPE html>
<html lang="en">
<head>
<meta charset="utf-8">
<title>Brightwell Retrofit Co. — Business Card</title>
<link rel="stylesheet" href="https://fonts.googleapis.com/css2?family=Montserrat:wght@500;600&family=Open+Sans:wght@400;600&display=swap">
<style>
  :root {
    --stage: #d9dcd9;
    --forest: #0f4d24;
    --forest-deep: #0a3a1a;
    --green: #1f8a36;
    --lime: #6cc04a;
    --ink: #5a5a5a;
    --paper: #ffffff;
  }
  * { box-sizing: border-box; margin: 0; padding: 0; }
  html, body { width: 1200px; height: 810px; overflow: hidden; }
  body {
    background: var(--stage);
    font-family: "Open Sans", Arial, sans-serif;
    position: relative;
  }
  .card {
    position: absolute;
    top: 250px;
    width: 540px;
    height: 309px;
    overflow: hidden;
    box-shadow: 0 10px 30px rgba(0,0,0,.18);
  }
  /* Front */
  .card--front {
    left: 40px;
    background: radial-gradient(ellipse at 50% 40%, #17622f 0%, var(--forest) 55%, var(--forest-deep) 100%);
    color: var(--paper);
    text-align: center;
  }
  .brand {
    font-family: "Montserrat", Arial, sans-serif;
    font-weight: 600;
    letter-spacing: .02em;
    display: inline-flex;
    align-items: center;
    gap: 12px;
  }
  .brand__mark {
    width: 16px; height: 16px;
    background: var(--lime);
  }
  .card--front .brand {
    margin-top: 118px;
    font-size: 30px;
    color: var(--paper);
  }
  .card--front .rule {
    width: 300px;
    height: 1px;
    background: rgba(255,255,255,.55);
    margin: 14px auto 0;
  }
  .card--front .web {
    margin-top: 66px;
    font-size: 13px;
    letter-spacing: .12em;
    color: var(--lime);
  }
  /* Back */
  .card--back {
    left: 620px;
    background: var(--paper);
  }
  .card--back .brand {
    position: absolute;
    top: 34px;
    right: 30px;
    font-size: 20px;
    color: var(--forest);
  }
  .divider {
    position: absolute;
    left: 30px;
    right: 30px;
    top: 128px;
    height: 1.5px;
    background: var(--green);
  }
  .address {
    position: absolute;
    right: 30px;
    top: 84px;
    text-align: right;
    font-size: 12.5px;
    line-height: 1.4;
    color: var(--ink);
  }
  .person {
    position: absolute;
    left: 30px;
    top: 146px;
  }
  .person__name {
    font-family: "Montserrat", Arial, sans-serif;
    font-weight: 500;
    font-size: 20px;
    color: var(--green);
    letter-spacing: .02em;
  }
  .person__role {
    font-size: 16px;
    color: var(--ink);
  }
  .contacts {
    position: absolute;
    left: 30px;
    top: 208px;
    list-style: none;
    border-top: 1.5px solid var(--green);
    padding-top: 8px;
    width: 240px;
  }
  .contacts li {
    display: flex;
    align-items: center;
    gap: 12px;
    font-size: 13px;
    line-height: 1.55;
    color: var(--ink);
  }
  .contacts svg { width: 11px; height: 11px; fill: var(--green); flex: none; }
  .band {
    position: absolute;
    left: 0; right: 0; bottom: 0;
    height: 12px;
    display: flex;
  }
  .band__dark { flex: 0 0 52%; background: var(--green); }
  .band__light { flex: 1; background: var(--lime); margin-left: 3px; }
</style>
</head>
<body>
  <section class="card card--front" aria-label="Card front">
    <div class="brand"><span class="brand__mark"></span>Brightwell Retrofit Co.</div>
    <div class="rule"></div>
    <p class="web">www.brightwellretrofit.com</p>
  </section>

  <section class="card card--back" aria-label="Card back">
    <div class="brand"><span class="brand__mark"></span>Brightwell Retrofit Co.</div>
    <p class="address">4870 Harbor Lane,<br>Suite Mesa 85201</p>
    <div class="divider"></div>
    <div class="person">
      <p class="person__name">DANIEL REYES</p>
      <p class="person__role">Founder</p>
    </div>
    <ul class="contacts">
      <li><svg viewBox="0 0 24 24"><path d="M6.6 10.8a15 15 0 0 0 6.6 6.6l2.2-2.2a1 1 0 0 1 1-.25 11.4 11.4 0 0 0 3.6.57 1 1 0 0 1 1 1V20a1 1 0 0 1-1 1A17 17 0 0 1 3 4a1 1 0 0 1 1-1h3.5a1 1 0 0 1 1 1c0 1.25.2 2.45.57 3.57a1 1 0 0 1-.25 1z"/></svg>0400 555 019</li>
      <li><svg viewBox="0 0 24 24"><path d="M2 5h20v14H2zm2 2v.5l8 5 8-5V7l-8 5z"/></svg>hello@brightwellretrofit.com</li>
      <li><svg viewBox="0 0 24 24"><path d="M12 2a10 10 0 1 0 0 20 10 10 0 0 0 0-20zm0 2c.9 1.2 1.6 2.6 2 4h-4c.4-1.4 1.1-2.8 2-4zM4.3 14a8 8 0 0 1 0-4h3.4a16 16 0 0 0 0 4zm.9 2h3c.3 1.3.8 2.5 1.4 3.5A8 8 0 0 1 5.2 16zm3-8h-3a8 8 0 0 1 4.4-3.5C8 5.5 7.6 6.7 8.2 8zM12 20c-.9-1.2-1.6-2.6-2-4h4c-.4 1.4-1.1 2.8-2 4zm2.3-6H9.7a14 14 0 0 1 0-4h4.6a14 14 0 0 1 0 4zm.1 5.5c.6-1 1.1-2.2 1.4-3.5h3a8 8 0 0 1-4.4 3.5zM16.3 14a16 16 0 0 0 0-4h3.4a8 8 0 0 1 0 4zm-.5-6c-.3-1.3-.8-2.5-1.4-3.5A8 8 0 0 1 18.8 8z"/></svg>www.brightwellretrofit.com</li>
    </ul>
    <div class="band"><span class="band__dark"></span><span class="band__light"></span></div>
  </section>
</body>
</html>
```